Residential real estate home builder in west texas

We need a website design for our home building business based in west Texas called Birch Hollow homes. We build new construction for potential homeowners in Amarillo. Currently we do not have any completed construction, but we have floor plans and architectural drawings of the front elevation. The website would need to be able to properly advertise a architectural drawing, floor plans, and descriptive content at the initial phase. The website will need to be simple but professional with generic picture content.
The website will need the ability to be updated in the future for the additions of home pictures, and video content and virtual tours of the homes.

Target Market(s)

Potential Home buyers

Industry/Entity Type

Real Estate

Number of Pages Required

5+ page

Font styles to use
Sans Serif

Colors
f37122
757575

Requirements
Must have
• Web design must be simple and easy to navigate. There is not much picture content, so it will need to be simple.
• 5 pages:
• Home, Available homes, Available floor plans, guide to ownership, Contact
• The website will need the ability to be updated in the future for the additions of pictures, and video content of the homes when they are built. ( A virtual tour).
Nice to have
• I would like to see a modern and cohesive design. Contact information at the bottom of each page.
Should not have
• A Black background

```html
<!DOCTYPE html>
<html lang="en">
<head>
<meta charset="utf-8">
<title>Birch Hollow Homes</title>
<link href="https://fonts.googleapis.com/css2?family=Montserrat:wght@400;500;600&family=Open+Sans:wght@400;600&display=swap" rel="stylesheet">
<style>
:root{
  --orange:#f37122;
  --orange-deep:#e4502a;
  --grey:#757575;
  --ink:#444a55;
  --light:#f7f7f7;
  --footer:#f3f4f6;
  --bar:#5b5c6e;
  --line:#e2e2e2;
}
*{margin:0;padding:0;box-sizing:border-box}
html,body{width:1200px;height:2557px;overflow:hidden;background:#fff}
body{font-family:"Open Sans",Arial,sans-serif;color:var(--grey);position:relative}
.abs{position:absolute}
h1,h2,h3,h4,.nav a,.btn,.more{font-family:"Montserrat",Arial,sans-serif}
p{font-size:12.5px;line-height:25px}

/* header */
.header{left:0;top:0;width:1200px;height:88px;background:#fff}
.brand{left:85px;top:30px;font-family:"Montserrat",sans-serif;font-weight:600;font-size:19px;line-height:26px;color:var(--orange);display:flex;align-items:center;gap:9px;white-space:nowrap}
.brand .dot{width:12px;height:12px;background:var(--orange)}
.nav{left:360px;top:36px}
.nav a{font-size:12.5px;font-weight:500;color:#555;text-decoration:none;letter-spacing:.3px;position:absolute;white-space:nowrap}
.nav a.active{color:var(--orange)}
.search{left:1064px;top:20px;width:48px;height:48px;border:1.5px solid var(--orange);border-radius:50%}

/* hero */
.hero{left:0;top:88px;width:1200px;height:515px;background:linear-gradient(180deg,#8fb6dc 0%,#b9cde0 35%,#7a6a5e 55%,#6f8a4a 80%,#7fa24e 100%)}
.hero-card{left:755px;top:290px;width:358px;height:210px;background:rgba(95,95,105,.72);padding:24px 22px}
.hero-card h2{font-size:26px;font-weight:500;color:#fff;margin-bottom:12px}
.hero-card p{font-size:11.5px;line-height:22px;color:#fff}
.hero-card .more{display:inline-block;margin-top:12px;color:#fff;font-size:14px;font-weight:500;border-bottom:2px solid #fff}
.dots{left:1020px;top:468px;display:flex;gap:7px}
.dots span{width:15px;height:15px;border:2px solid #fff;border-radius:50%}
.dots span.on{background:var(--orange)}

/* welcome */
.welcome{left:0;top:603px;width:1200px;height:271px;background:linear-gradient(180deg,#ee7440,var(--orange-deep));text-align:center;color:#fff}
.welcome h3{font-size:20px;font-weight:500;margin-top:32px;letter-spacing:1px}
.welcome h2{font-size:29px;font-weight:500;margin-top:8px}
.welcome p{width:730px;margin:16px auto 0;font-size:12px;line-height:26px}
.btn-outline-white{display:inline-block;margin-top:22px;padding:11px 20px;border:1.5px solid #fff;color:#fff;font-size:14px;font-weight:500}

/* services */
.section-title{font-size:22px;font-weight:500;color:var(--orange);text-align:center}
.services-title{left:0;top:906px;width:1200px}
.services-sub{left:0;top:944px;width:1200px;text-align:center;font-size:12px}
.card{top:1000px;width:330px;height:410px;border:1px solid var(--line);background:#fff;text-align:center}
.card .photo{height:235px;position:relative}
.card svg{position:absolute;left:0;bottom:0}
.card h4{font-size:16px;font-weight:500;color:var(--orange);margin-top:16px}
.card p{padding:0 18px;margin-top:8px;font-size:11.5px}
.card .more{display:inline-block;margin-top:14px;font-size:12.5px;font-weight:600;color:var(--orange);border-bottom:1.5px solid var(--orange)}

/* video */
.video-band{left:0;top:1461px;width:1200px;height:407px;background:var(--light)}
.video{left:85px;top:1512px;width:490px;height:296px;background:linear-gradient(160deg,#9fbfdc,#b8b4a8 55%,#7f6a58)}
.video .play{left:212px;top:116px;width:64px;height:46px;background:#e0261f;border-radius:10px}
.video .controls{left:0;bottom:0;width:490px;height:22px;background:#222}
.video .progress{left:0;bottom:22px;width:490px;height:4px;background:#d42}
.video-text{left:610px;top:1522px;width:500px}
.video-text h2{font-size:20px;font-weight:500;color:var(--ink);margin-bottom:18px}
.video-text p{font-size:11.5px;margin-bottom:16px}
.btn-solid{display:inline-block;padding:13px 26px;background:var(--orange);color:#fff;font-size:14px;font-weight:500;border-radius:2px;margin-top:6px}

/* tours & testimonial */
.block-title{font-size:20px;font-weight:500;color:var(--ink)}
.tours{left:87px;top:1918px;width:380px}
.tours p{margin-top:22px;font-size:11.5px}
.btn-outline{display:inline-block;margin-top:22px;padding:11px 21px;border:1.5px solid var(--orange);color:var(--orange);font-size:13px;font-weight:500}
.testimonial{left:516px;top:1918px;width:600px}
.avatar{left:517px;top:1974px;width:126px;height:126px;border-radius:50%;background:radial-gradient(circle at 50% 40%,#d8a98c,#7a4b33 70%)}
.quote{left:678px;top:1990px;width:435px}
.quote p{font-size:11.5px;line-height:24px}
.qmark{font-family:Georgia,serif;font-size:30px;color:var(--grey);position:absolute}
.qmark-end{font-family:Georgia,serif;font-size:24px;line-height:10px;color:var(--grey);margin-left:4px;vertical-align:-8px}
.author{left:681px;top:2116px}
.author b{font-family:"Montserrat",sans-serif;font-weight:500;color:var(--orange);font-size:13px;display:block}
.author span{font-size:13px}

/* footer */
.footer{left:0;top:2216px;width:1200px;height:273px;background:var(--footer)}
.foot-brand{left:90px;top:2358px;font-family:"Montserrat",sans-serif;font-weight:600;font-size:26px;color:var(--orange);white-space:nowrap}
.foot-col{top:2274px}
.foot-col h4{font-size:15px;font-weight:500;color:var(--ink);margin-bottom:22px}
.foot-col li{list-style:none;font-size:12px;color:#666;display:flex;gap:14px;margin-bottom:13px;line-height:17px}
.foot-col li svg{flex:none;margin-top:2px}
.foot-col p{font-size:11.5px;line-height:21px}
.email{margin-top:14px;width:212px;height:34px;border:1px solid #ccc;background:#fff;font-size:12px;padding:9px 12px;color:#666}
.subscribe{display:inline-block;margin-top:10px;background:var(--orange);color:#fff;font-size:11px;padding:7px 11px;font-family:"Montserrat",sans-serif}
.social{display:flex;gap:8px;margin-top:14px}
.social span{width:36px;height:36px;border:1.5px solid #aaa;border-radius:50%}
.bottom-bar{left:0;top:2489px;width:1200px;height:68px;background:var(--bar);color:#fff;text-align:center;font-size:12px;line-height:68px}
</style>
</head>
<body>

<header class="abs header">
  <div class="abs brand"><span class="dot"></span>Birch Hollow Homes</div>
  <nav class="abs nav">
    <a class="active" style="left:0">HOME</a>
    <a style="left:82px">AVAILABLE HOMES</a>
    <a style="left:243px">AVAILABLE FLOOR PLANS</a>
    <a style="left:446px">GUIDE TO OWNERSHIP</a>
    <a style="left:629px">CONTACT</a>
  </nav>
  <div class="abs search">
    <svg width="48" height="48" viewBox="0 0 48 48"><circle cx="22" cy="22" r="5" fill="none" stroke="#f37122" stroke-width="2"/><line x1="26" y1="26" x2="30" y2="30" stroke="#f37122" stroke-width="2"/></svg>
  </div>
</header>

<section class="abs hero" role="img" aria-label="Photo of a craftsman style new home with landscaped front yard">
</section>
<div class="abs hero-card">
  <h2>BIRCH HOLLOW HOME</h2>
  <p>Sed ut perspiciatis unde omnis iste natus error sit voluptatem accusantium doloremque laudantium, totam rem architecto beatae vitae dicta sunt explicabo.</p>
  <span class="more">READ MORE</span>
</div>
<div class="abs dots"><span></span><span class="on"></span><span></span></div>

<section class="abs welcome">
  <h3>— WELCOME TO —</h3>
  <h2>BIRCH HOLLOW HOME</h2>
  <p>Sed ut perspiciatis unde omnis iste natus error sit voluptatem accusantium doloremque laudantium, totam rem aperiam, eaque ipsa quae ab illo inventore veritatis et quasi architecto beatae vitae dicta sunt explicabo. Nemo enim ipsam voluptatem quia voluptas sit aspernatur aut odit aut fugit, sed quia consequuntur magni dolores eos qui ratione voluptatem sequi nesciunt.</p>
  <span class="btn-outline-white">READ MORE</span>
</section>

<h2 class="abs section-title services-title">OUR SERVICES</h2>
<p class="abs services-sub">Sed ut perspiciatis unde omnis iste natus error sit voluptatem accusantium doloremque laudantium, totam rem aperiam</p>

<article class="abs card" style="left:85px">
  <div class="photo" role="img" aria-label="Photo of a construction site with crane and concrete columns" style="background:linear-gradient(170deg,#9ec0e0,#a9a59a 60%,#6c6052)">
    <svg width="330" height="30" viewBox="0 0 330 30"><polygon points="0,30 0,20 165,0 330,20 330,30 320,30 320,24 165,10 10,24 10,30" fill="#e4502a"/><polygon points="10,30 10,24 165,10 320,24 320,30" fill="#fff"/></svg>
  </div>
  <h4>HOME BUILDING</h4>
  <p>Sed ut perspiciatis unde omnis iste natus error sit voluptatem accusantium doloremque laudantium, totam beatae vitae dicta sunt explicabo.</p>
  <span class="more">READ MORE ›</span>
</article>
<article class="abs card" style="left:436px">
  <div class="photo" role="img" aria-label="Photo of a construction worker in a hard hat on site" style="background:linear-gradient(170deg,#a8c4df,#b08a5e 60%,#5d5045)">
    <svg width="330" height="30" viewBox="0 0 330 30"><polygon points="0,30 0,20 165,0 330,20 330,30 320,30 320,24 165,10 10,24 10,30" fill="#e4502a"/><polygon points="10,30 10,24 165,10 320,24 320,30" fill="#fff"/></svg>
  </div>
  <h4>CONSTRUCTION</h4>
  <p>Sed ut perspiciatis unde omnis iste natus error sit voluptatem accusantium doloremque laudantium, totam beatae vitae dicta sunt explicabo.</p>
  <span class="more">READ MORE ›</span>
</article>
<article class="abs card" style="left:786px">
  <div class="photo" role="img" aria-label="Photo of a desk with architectural drawings and drafting tools" style="background:linear-gradient(170deg,#f2f2f2,#dedede 60%,#c9c9c9)">
    <svg width="330" height="30" viewBox="0 0 330 30"><polygon points="0,30 0,20 165,0 330,20 330,30 320,30 320,24 165,10 10,24 10,30" fill="#e4502a"/><polygon points="10,30 10,24 165,10 320,24 320,30" fill="#fff"/></svg>
  </div>
  <h4>ARCHITECTURAL DRAWING</h4>
  <p>Sed ut perspiciatis unde omnis iste natus error sit voluptatem accusantium doloremque laudantium, totam beatae vitae dicta sunt explicabo.</p>
  <span class="more">READ MORE ›</span>
</article>

<section class="abs video-band"></section>
<div class="abs video" role="img" aria-label="Video still of a construction site with a crane">
  <div class="abs play"><svg width="64" height="46" viewBox="0 0 64 46"><polygon points="25,14 25,32 40,23" fill="#fff"/></svg></div>
  <div class="abs progress"></div>
  <div class="abs controls"><svg width="490" height="22" viewBox="0 0 490 22"><polygon points="14,6 14,16 22,11" fill="#ccc"/><rect x="40" y="8" width="8" height="6" fill="#ccc"/><rect x="462" y="6" width="10" height="10" fill="none" stroke="#ccc" stroke-width="1.5"/></svg></div>
</div>
<div class="abs video-text">
  <h2>FEATURED VIDEO</h2>
  <p>Sed ut perspiciatis unde omnis iste natus error sit voluptatem accusantium doloremque laudan tium, totam rem aperiam, eaque ipsa quae ab illo inventore veritatis et quasi architecto bea tae vitae dicta sunt explicabo. Nemo enim ipsam voluptatem quia volup magni dolores eos qui ratione voluptatem sequi nesciunt.</p>
  <p>Sed ut perspiciatis unde omnis iste natus error sit voluptatem accusantium doloremque lauea que ipsa quae ab illo inventorebeatae vitae dicta sunt explicabo.</p>
  <span class="btn-solid">READ MORE</span>
</div>

<div class="abs tours">
  <h2 class="block-title">OUR VIRTUAL TOURS</h2>
  <p>Sed ut perspiciatis unde omnis iste natus error sit voluptatem accusantium doloremque laudantium, totam rem aperiam, eaque ipsa quae ab illo inventore veritatis et quasi architecto beatae vitae dicta sunt explicabo. Nemo enim ipsam voluptatem quia voluptas sit aspernatur aut odit aut fugit, sed quia consequuntur magni dolores eos qui ratione voluptatem sequi nesciunt.</p>
  <span class="btn-outline">READ MORE</span>
</div>
<div class="abs testimonial"><h2 class="block-title">OUR TESTIMONIALS</h2></div>
<div class="abs avatar" role="img" aria-label="Portrait photo of a smiling customer"></div>
<div class="abs quote">
  <span class="qmark" style="left:-17px;top:-10px">“</span>
  <p>Sed ut perspiciatis unde omnis iste natus error sit voluptatem accusan tium doloremque laudantium, totam rem aperiam, eaque ipsa quae ab illo inventore veritatis et quasi architecto beatae vitae dicta sunt explicabo. Nemo enim ipsam voluptatem quia volup magni dolores eos qui ratione voluptatem sequi nesciunt.<span class="qmark-end">”</span></p>
</div>
<div class="abs author"><b>Name : Clara Dunn</b><span>Posted on 13 July 2017</span></div>

<footer class="abs footer"></footer>
<div class="abs foot-brand">Birch Hollow Homes</div>
<div class="abs foot-col" style="left:396px;width:210px">
  <h4>CONTACT US</h4>
  <ul>
    <li><svg width="14" height="14" viewBox="0 0 14 14"><rect x="1" y="4" width="12" height="9" rx="1" fill="#666"/><rect x="3" y="1" width="8" height="4" rx="1" fill="#666"/></svg>(000)-121-1231 (Phone)</li>
    <li><svg width="14" height="14" viewBox="0 0 14 14"><rect x="1" y="5" width="12" height="7" rx="1" fill="#666"/><rect x="3" y="1" width="8" height="4" fill="none" stroke="#666"/></svg>(000)-121-1231 (Fax)</li>
    <li><svg width="14" height="14" viewBox="0 0 14 14"><rect x="1" y="3" width="12" height="9" fill="#666"/><polyline points="1,3 7,8 13,3" fill="none" stroke="#fff"/></svg><u>info@birchhollowhomes.com</u></li>
    <li><svg width="14" height="14" viewBox="0 0 14 14"><path d="M7 1a4 4 0 0 1 4 4c0 3-4 8-4 8S3 8 3 5a4 4 0 0 1 4-4z" fill="#666"/><circle cx="7" cy="5" r="1.5" fill="#f3f4f6"/></svg>70 Lorem Ipsum Dummy Text<br>Lorem Ipsum</li>
  </ul>
</div>
<div class="abs foot-col" style="left:643px;width:220px">
  <h4>NEWSLETTER</h4>
  <p>Register Your email address to get information ablout us</p>
  <div class="email">Email Address</div>
  <span class="subscribe">SUBSCRIBE</span>
</div>
<div class="abs foot-col" style="left:895px;width:220px">
  <h4>FOLLOW US</h4>
  <p>Lorem ipsum dolor sit amet, conse ctetur adipiscing elit. Nulla in purus nibh. Donec ornare</p>
  <div class="social"><span></span><span></span><span></span><span></span><span></span></div>
</div>
<div class="abs bottom-bar">© Copyright 2017 Birch Hollow homes.All Rights Reserved</div>

</body>
</html>
```